Clean & Inspiring Web Design Project

Tallowmere Object Works, LLC (also known as T7-Works) is a company which provides 3D printing services and products. The emphasis is on making these products and services available to the mass-market - customers and users who may or may not have prior experience with 3D printing and/or rapid prototyping technologies. We are a start-up company, looking to build a clean and creativity inspiring brand - our site must encourage visitor to engage and make something. Our aim is to help take mere ideas and turn them into tangible items. We want to show a fusion of ideas (e.g. pencil sketches on graph paper) with design tools (e.g. CAD and drafting software) and rapid prototyping (e.g. Kindlo 3D printers, Stereolithography Machines, etc.). We would like the website to appear professional but at the same time easy to navigate and a good balance between text and pictures. The final design should inspire customers to nurture their ideas into real products and communicate our services to our customers. Our site should have the feel of a vibrant social community with the added benefit of tangible physical creations.

Target Market(s)

People with great ideas that need to be designed into a real product

Industry/Entity Type

Printing

Requirements
Must have
• - Website design should include 2 layouts - one for a "landing page" and one for a "content page"
- Website design must incorporate attached company logo (or derivative of this logo)
- Website design should incorporate the menu options shown in the attached PDF UI concept (UI does not necessarily need to look like the provided concept, just include all the clickable elements)
- Website design must portray an innovative and cooperative design environment with a look-and-feel that appeals to both amateur and professional designers.
- Please include pictures, illustrations and photographs (as needed) related to 3D printing, CAD design, conventional drafting, engineering and manufacturing industries.
- Design should support scaling to multiple screen sizes, from tablet computers (e.g. Zelo) to very large screen PCs.
- Design should include Username & Password fields for login or a button to pull up a login popup.
Nice to have
• - Website design could include "Invent", "Make", "Produce" and "Buy" options that slowly cycle through - with appropriate photos / graphics. These "menu options" would also be mouse-over enabled to switch into the appropriate context as the cursor enters that region (e.g. mouse over the "Invent" text would bring up page 2, etc.). (See attached Original UI Thoughts)
Should not have
• Requirements - Should Not Have:
- Website design should not portray a service that is very expensive or complicated - we are a reasonably priced service meant to be friendly with amateur inventors
- Website design should not be overly complicated - please keep it reasonably simple
- Website design should not be overly trendy
- Website design should not use more than 2 font styles, gaudy fonts, etc.
- Website design should not be "campy" or "tacky" - playful is ok, but please keep it elegant
- Website design should not be overly masculine or feminine - we will have both women and men as customers

```html
<!DOCTYPE html>
<html lang="en">
<head>
<meta charset="utf-8">
<title>Tallowmere Object Works, LLC – About T7</title>
<link rel="stylesheet" href="https://fonts.googleapis.com/css2?family=Source+Sans+3:wght@400;600;700&display=swap">
<style>
:root{
  --ink:#1d1d1d;
  --text:#4a4a4a;
  --blue:#1a7cc1;
  --navy:#0d4e7e;
  --nav-top:#14619a;
  --nav-bot:#0b4a78;
  --orange:#f28a1a;
  --gold:#f6a81b;
  --dark:#2a2a2a;
  --darker:#1b1b1b;
  --line:#d6d6d6;
  --tick:#3aa63a;
  --step1:#0f6a9f;
  --step2:#167fbc;
  --step3:#2294d1;
}
*{box-sizing:border-box;margin:0;padding:0}
html,body{width:1051px;height:1200px;overflow:hidden;background:#fff}
body{font-family:"Source Sans 3",sans-serif;color:var(--text)}
.page{position:absolute;left:0;top:0;width:1200px;height:1370px;transform:scale(0.87583);transform-origin:0 0}
.abs{position:absolute}

.topbar{left:0;top:0;width:1200px;height:28px;background:linear-gradient(#2f2f2f,#171717)}
.topnav{left:321px;top:8px;display:flex;gap:19px;font-size:9px;color:#ddd;letter-spacing:.1px}
.topnav .on{color:#fff;position:relative}
.topnav .on::after{content:"";position:absolute;left:11px;top:14px;border:4px solid transparent;border-bottom-color:var(--orange)}
.search-ico{left:554px;top:7px}
.search{left:574px;top:5px;width:181px;height:17px;background:#fff;border-radius:3px;font-size:7px;color:#999;padding:4px 7px}
.account{left:780px;top:8px;font-size:9px;color:#eee}
.account i{font-style:italic}

.header{left:0;top:28px;width:1200px;height:157px;background:linear-gradient(#a9d3ee 0%,#d9ecf8 60%,#fff 100%)}
.brand-mark{left:310px;top:48px;width:54px;height:54px;background:var(--navy);border-radius:4px}
.brand-name{left:374px;top:60px;font-size:25px;color:var(--blue);font-weight:400;white-space:nowrap}
.brand-tag{left:374px;top:88px;font-size:14px;color:var(--blue)}

.navshadow{left:210px;top:176px;width:780px;height:10px;background:radial-gradient(ellipse at 50% 0,rgba(0,0,0,.25),rgba(0,0,0,0) 70%)}
.mainnav{left:294px;top:138px;width:618px;height:45px;background:linear-gradient(var(--nav-top),var(--nav-bot))}
.home{left:0;top:0;width:52px;height:45px;background:var(--orange)}
.home-tip{left:52px;top:0;width:0;height:0;border-top:22.5px solid transparent;border-bottom:22.5px solid transparent;border-left:9px solid var(--orange)}
.tab{top:14px;font-size:9px;color:#fff;font-weight:600}
.tab small{display:block;font-size:7px;color:#7fb1d6;font-weight:400;margin-top:1px;white-space:nowrap}
.tab-active{left:60px;top:4px;width:74px;height:41px;background:#fff;border-top:3px solid var(--orange);padding:9px 0 0 12px;color:var(--ink);font-size:9px;font-weight:600}
.tab-active small{display:block;font-size:7px;color:#999;font-weight:400}
.cartzone{left:428px;top:0;width:190px;height:45px;border-left:1px solid #0a3c62}
.cart-label{left:49px;top:13px;font-size:8px;color:#fff;font-weight:600;line-height:10px}
.cart-label span{color:var(--gold)}
.shop-btn{left:91px;top:9px;width:90px;height:28px;background:linear-gradient(#ffbf2e,#f29a10);border:1px solid #d98a0e;font-size:11px;color:#2a1a00;font-weight:600;text-align:center;line-height:26px}

.crumb{left:300px;top:190px;font-size:8px;color:#555}
.crumb span{color:var(--orange)}
.crumb-rule{left:294px;top:203px;width:619px;height:1px;background:var(--line)}

.photo{background:linear-gradient(135deg,#8a7a6c,#5a4e44 55%,#3d342d)}
.about-photo{left:300px;top:225px;width:245px;height:163px;border:1px solid #bbb}
h1,h2{font-weight:400;color:var(--ink)}
.about-title{left:561px;top:222px;font-size:14px}
.copy{font-size:8px;line-height:13px;color:var(--text)}
.about-copy{left:561px;top:249px;width:338px}
.about-copy p+p{margin-top:13px}

.sec-title{font-size:14px}
.sec-sub{font-size:10px;color:var(--blue)}
.wide{left:300px;width:604px}
.checks{display:flex;flex-direction:column;gap:6px;font-size:8px;color:#333}
.checks li{list-style:none;display:flex;align-items:center;gap:7px;height:13px}

.steps{left:301px;top:770px}
.step-text{font-size:8px;color:#e4f2fb;line-height:11px;width:118px}
.step-title{font-size:15px;color:#fff;font-weight:700}

.divider{left:415px;top:930px;width:375px;height:12px;background:radial-gradient(ellipse at 50% 0,rgba(0,0,0,.18),rgba(0,0,0,0) 70%);border-top:1px solid #ddd}

.product{width:150px}
.product .frame{width:150px;height:91px;border:1px solid #ddd;box-shadow:0 2px 3px rgba(0,0,0,.15);background:#fff;padding:3px}
.product .frame div{width:100%;height:100%}
.product h3{font-size:11px;font-weight:400;color:var(--ink);margin-top:13px}
.product p{font-size:8px;color:#555;line-height:11px;margin-top:4px}
.more-note{left:710px;top:1128px;font-size:8px;color:#333}
.more-btn{left:812px;top:1118px;width:81px;height:26px;background:#1c1c1c;color:#fff;font-size:11px;text-align:center;line-height:26px;border-radius:2px;box-shadow:0 2px 3px rgba(0,0,0,.4)}

.footer{left:0;top:1168px;width:1200px;height:202px;background:linear-gradient(var(--dark),var(--darker))}
.foot-card{left:300px;top:1168px;width:300px;height:110px;background:#fff;border-radius:0 0 5px 5px}
.foot-mark{left:10px;top:30px;width:54px;height:60px;background:var(--navy);border-radius:4px}
.foot-name{left:74px;top:32px;font-size:16px;color:var(--blue);white-space:nowrap}
.foot-tag{left:74px;top:55px;font-size:12px;color:var(--blue);line-height:14px}
.foot-links{left:636px;top:1199px;font-size:9px;color:#fff;display:flex;gap:7px}
.foot-links b{font-weight:400;color:#bbb}
.foot-photo{left:635px;top:1229px;width:115px;height:79px;background:#fff;padding:4px}
.foot-photo div{width:100%;height:100%}
.foot-title{left:759px;top:1227px;font-size:9px;color:#fff}
.foot-copy{left:759px;top:1246px;width:138px;font-size:8px;color:#888;line-height:11px}
.read-btn{left:829px;top:1286px;width:64px;height:24px;background:var(--navy);color:#fff;font-size:10px;text-align:center;line-height:24px}
.social{left:312px;top:1289px;display:flex;gap:8px}
.social span{width:22px;height:22px;border:1px solid #777;background:#444;border-radius:2px;display:block}
.legal{left:312px;top:1329px;font-size:7px;color:#5d8fb5}
</style>
</head>
<body>
<div class="page">

  <div class="abs topbar"></div>
  <nav class="abs topnav"><span class="on">WHY T7</span><span>DREAMER</span><span>MAKER</span><span>PRODUCER</span></nav>
  <svg class="abs search-ico" width="14" height="14" viewBox="0 0 14 14"><circle cx="8" cy="6" r="4" fill="none" stroke="#f28a1a" stroke-width="2"/><path d="M5 9L1 13" stroke="#f28a1a" stroke-width="2"/></svg>
  <div class="abs search">Type search here...</div>
  <div class="abs account"><i>Hello Guest</i>, Login &nbsp;|&nbsp; Register</div>

  <header class="abs header"></header>
  <div class="abs brand-mark"></div>
  <div class="abs brand-name">Tallowmere Object Works, LLC</div>
  <div class="abs brand-tag">Bringing Your Ideas to Market</div>

  <div class="abs navshadow"></div>
  <nav class="abs mainnav">
    <div class="abs home">
      <svg width="52" height="45" viewBox="0 0 52 45"><path d="M13 23L24 13L35 23" fill="none" stroke="#fff" stroke-width="3"/><path d="M16 22V32H22V26H26V32H32V22" fill="#fff"/></svg>
    </div>
    <div class="abs home-tip"></div>
    <div class="abs tab-active">ABOUT T7<small>Nam liber temp</small></div>
    <div class="abs tab" style="left:152px">DREAM<small>Nobis eleifend</small></div>
    <div class="abs tab" style="left:222px">MAKE<small>Dolor sit amet</small></div>
    <div class="abs tab" style="left:284px">PRODUCE<small>Adipiscing conec</small></div>
    <div class="abs tab" style="left:364px">SELL<small>Ed deli vero</small></div>
    <div class="abs cartzone">
      <svg class="abs" style="left:12px;top:8px" width="30" height="28" viewBox="0 0 30 28"><path d="M1 3H6L10 18H25L28 7H8" fill="none" stroke="#dfe9f1" stroke-width="2"/><path d="M9 8H27L25 16H11Z" fill="#9fb9cc"/><circle cx="12" cy="23" r="2.5" fill="#dfe9f1"/><circle cx="23" cy="23" r="2.5" fill="#dfe9f1"/></svg>
      <div class="abs cart-label">Shopping<br>Chart <span>(0)</span></div>
      <div class="abs shop-btn">Shopping NOW!</div>
    </div>
  </nav>

  <div class="abs crumb">You at : <span>About T7</span></div>
  <div class="abs crumb-rule"></div>

  <div class="abs about-photo photo" role="img" aria-label="Photo of a 3D printed lattice high-heel shoe worn on a wooden floor"></div>
  <h1 class="abs about-title">ABOUT T7</h1>
  <div class="abs about-copy copy">
    <p>Duis autem vel eum iriure dolor in hendrerit in vulputate velit esse molestie consequat, vel illum dolore eu feugiat nulla facilisis at vero eros et accumsan et iusto odio dignissim qui blandit praesent luptatum zzril delenit augue duis dolore te feugait nulla facilisi. Lorem ipsum dolor sit amet, consectetuer adipiscing elit, sed diam nonummy nibh euismod tincidunt ut laoreet dolore magna aliquam erat volutpat.</p>
    <p>Ut wisi enim ad minim veniam, quis nostrud exerci tation ullamcorper suscipit lobortis nisl ut aliquip ex ea commodo consequat. Duis autem vel eum iriure dolor in hendrerit in vulputate velit esse molestie consequat, vel illum dolore eu feugiat nulla facilisis at vero eros et accumsan et iusto odio dignissim qui blandit praesent luptatum zzril delenit augue</p>
  </div>

  <h2 class="abs sec-title" style="left:300px;top:426px">Why Choose Us?</h2>
  <div class="abs sec-sub" style="left:300px;top:444px">Better choise</div>
  <p class="abs wide copy" style="top:471px">Duis autem vel eum iriure dolor in hendrerit in vulputate velit esse molestie consequat, vel illum dolore eu feugiat nulla facilisis at vero eros et accumsan et iusto odio dignissim qui blandit praesent luptatum zzril delenit augue duis dolore te feugait nulla facilisi. Lorem ipsum dolor sit amet, consectetuer adipiscing elit, sed diam nonummy nibh euismod tincidunt ut laoreet dolore magna aliquam erat volutpat.</p>

  <ul class="abs checks" style="left:319px;top:525px">
    <li><svg width="9" height="8" viewBox="0 0 9 8"><path d="M1 4L3.5 6.5L8 1" fill="none" stroke="#3aa63a" stroke-width="2"/></svg>Nam liber tempor cum soluta.</li>
    <li><svg width="9" height="8" viewBox="0 0 9 8"><path d="M1 4L3.5 6.5L8 1" fill="none" stroke="#3aa63a" stroke-width="2"/></svg>Nobis eleifend option congue nihil.</li>
    <li><svg width="9" height="8" viewBox="0 0 9 8"><path d="M1 4L3.5 6.5L8 1" fill="none" stroke="#3aa63a" stroke-width="2"/></svg>Doming id quod mazim.</li>
    <li><svg width="9" height="8" viewBox="0 0 9 8"><path d="M1 4L3.5 6.5L8 1" fill="none" stroke="#3aa63a" stroke-width="2"/></svg>Lorem ipsum dolor sit amet.</li>
  </ul>
  <ul class="abs checks" style="left:500px;top:525px">
    <li><svg width="9" height="8" viewBox="0 0 9 8"><path d="M1 4L3.5 6.5L8 1" fill="none" stroke="#3aa63a" stroke-width="2"/></svg>Nam liber tempor cum soluta.</li>
    <li><svg width="9" height="8" viewBox="0 0 9 8"><path d="M1 4L3.5 6.5L8 1" fill="none" stroke="#3aa63a" stroke-width="2"/></svg>Nobis eleifend option congue nihil.</li>
    <li><svg width="9" height="8" viewBox="0 0 9 8"><path d="M1 4L3.5 6.5L8 1" fill="none" stroke="#3aa63a" stroke-width="2"/></svg>Doming id quod mazim.</li>
    <li><svg width="9" height="8" viewBox="0 0 9 8"><path d="M1 4L3.5 6.5L8 1" fill="none" stroke="#3aa63a" stroke-width="2"/></svg>Lorem ipsum dolor sit amet.</li>
  </ul>
  <ul class="abs checks" style="left:687px;top:525px">
    <li><svg width="9" height="8" viewBox="0 0 9 8"><path d="M1 4L3.5 6.5L8 1" fill="none" stroke="#3aa63a" stroke-width="2"/></svg>Nam liber tempor cum soluta.</li>
    <li><svg width="9" height="8" viewBox="0 0 9 8"><path d="M1 4L3.5 6.5L8 1" fill="none" stroke="#3aa63a" stroke-width="2"/></svg>Nobis eleifend option congue nihil.</li>
    <li><svg width="9" height="8" viewBox="0 0 9 8"><path d="M1 4L3.5 6.5L8 1" fill="none" stroke="#3aa63a" stroke-width="2"/></svg>Doming id quod mazim.</li>
    <li><svg width="9" height="8" viewBox="0 0 9 8"><path d="M1 4L3.5 6.5L8 1" fill="none" stroke="#3aa63a" stroke-width="2"/></svg>Lorem ipsum dolor sit amet.</li>
  </ul>

  <h2 class="abs sec-title" style="left:300px;top:635px">How to shop?</h2>
  <div class="abs sec-sub" style="left:300px;top:653px">Simple system</div>
  <p class="abs wide copy" style="top:680px">Duis autem vel eum iriure dolor in hendrerit in vulputate velit esse molestie consequat, vel illum dolore eu feugiat nulla facilisis at vero eros et accumsan et iusto odio dignissim qui blandit praesent luptatum zzril delenit augue duis dolore te feugait nulla facilisi. Lorem ipsum dolor sit amet, consectetuer adipiscing elit, sed diam nonummy nibh euismod tincidunt ut laoreet dolore magna aliquam erat volutpat. Lorem ipsum dolor sit amet, consectetuer adipiscing elit, sed diam nonummy nibh euismod tincidunt ut laoreet dolore magna aliquam erat volutpat.</p>

  <svg class="abs steps" width="610" height="140" viewBox="301 770 610 140" aria-label="Three shopping steps">
    <defs>
      <linearGradient id="g1" x1="0" y1="0" x2="0" y2="1"><stop offset="0" stop-color="#1679b3"/><stop offset="1" stop-color="#0c5f92"/></linearGradient>
      <linearGradient id="g2" x1="0" y1="0" x2="0" y2="1"><stop offset="0" stop-color="#1b8ccc"/><stop offset="1" stop-color="#1172ad"/></linearGradient>
      <linearGradient id="g3" x1="0" y1="0" x2="0" y2="1"><stop offset="0" stop-color="#2aa0dc"/><stop offset="1" stop-color="#1b86c3"/></linearGradient>
    </defs>
    <path d="M311 783H482L514 843L482 903H311Q301 903 301 893V793Q301 783 311 783Z" fill="url(#g1)"/>
    <path d="M493 783H672L704 843L672 903H493Q522 843 493 783Z" fill="url(#g2)"/>
    <path d="M683 783H879Q889 783 889 793V893Q889 903 879 903H683Q712 843 683 783Z" fill="url(#g3)"/>
    <text x="324" y="803" font-family="Source Sans 3, sans-serif" font-size="15" font-weight="700" fill="#fff">Choose product</text>
    <text x="544" y="801" font-family="Source Sans 3, sans-serif" font-size="15" font-weight="700" fill="#fff">Talk with Us</text>
    <text x="791" y="803" font-family="Source Sans 3, sans-serif" font-size="15" font-weight="700" fill="#fff">Payment</text>
    <g font-family="Source Sans 3, sans-serif" fill="#fff" text-anchor="middle">
      <circle cx="465" cy="791" r="20" fill="#111"/><text x="465" y="786" font-size="9">Step</text><text x="465" y="804" font-size="15">1</text>
      <circle cx="657" cy="791" r="20" fill="#111"/><text x="657" y="786" font-size="9">Step</text><text x="657" y="804" font-size="15">2</text>
      <circle cx="882" cy="791" r="20" fill="#111"/><text x="882" y="786" font-size="9">Step</text><text x="882" y="804" font-size="15">3</text>
    </g>
    <g>
      <path d="M318 829H324L329 857H354L358 838H326" fill="none" stroke="#dfe9f1" stroke-width="2.5"/>
      <path d="M327 839H357L353 855H330Z" fill="#a9c3d6"/>
      <circle cx="333" cy="865" r="3" fill="#dfe9f1"/><circle cx="351" cy="865" r="3" fill="#dfe9f1"/>
      <ellipse cx="545" cy="845" rx="17" ry="13" fill="#e6f3fb"/>
      <path d="M533 853L529 866L543 856Z" fill="#e6f3fb"/>
      <circle cx="538" cy="845" r="2" fill="#1b86c3"/><circle cx="545" cy="845" r="2" fill="#1b86c3"/><circle cx="552" cy="845" r="2" fill="#1b86c3"/>
      <rect x="712" y="832" width="44" height="35" rx="6" fill="#b8741a"/>
      <rect x="712" y="832" width="44" height="14" rx="6" fill="#d38f2b"/>
      <rect x="730" y="842" width="14" height="8" rx="2" fill="#f2c14a"/>
    </g>
    <g font-family="Source Sans 3, sans-serif" font-size="8" fill="#e4f2fb">
      <text x="370" y="844">Duis autem vel eum iriure dolor</text>
      <text x="370" y="855">in hendrerit in vulputate velit</text>
      <text x="370" y="866">esse molestie consequat.</text>
      <text x="572" y="844">Duis autem vel eum iriure dolor</text>
      <text x="572" y="855">in hendrerit in vulputate velit</text>
      <text x="572" y="866">esse molestie consequat.</text>
      <text x="766" y="844">Duis autem vel eum iriure dolor</text>
      <text x="766" y="855">in hendrerit in vulputate velit</text>
      <text x="766" y="866">esse molestie consequat.</text>
    </g>
  </svg>

  <div class="abs divider"></div>

  <article class="abs product" style="left:294px;top:962px">
    <div class="frame"><div style="background:radial-gradient(circle,#9a9a9a,#e8e8e8 70%)" role="img" aria-label="3D printed lattice rings"></div></div>
    <h3>Product 1</h3><p>Nam liber tempor cum soluta<br>nobis eleifend</p>
  </article>
  <article class="abs product" style="left:450px;top:962px">
    <div class="frame"><div style="background:radial-gradient(circle,#d8d6ce,#f4f4f2 70%)" role="img" aria-label="White 3D printed mechanical part"></div></div>
    <h3>Product 1</h3><p>Nam liber tempor cum soluta<br>nobis eleifend</p>
  </article>
  <article class="abs product" style="left:607px;top:962px">
    <div class="frame"><div style="background:linear-gradient(135deg,#3b3b3b,#e0603a 45%,#4e7fb8 75%,#eee)" role="img" aria-label="Assorted colourful printed plastic parts"></div></div>
    <h3>Product 1</h3><p>Nam liber tempor cum soluta<br>nobis eleifend</p>
  </article>
  <article class="abs product" style="left:763px;top:962px">
    <div class="frame" style="padding:0"><div style="background:linear-gradient(#c9a27a,#e2c7a5 50%,#b88b60)" role="img" aria-label="Close-up of a wavy printed surface texture"></div></div>
    <h3>Product 1</h3><p>Nam liber tempor cum soluta<br>nobis eleifend</p>
  </article>

  <div class="abs more-note">Please see our all product</div>
  <div class="abs more-btn">Find out more!</div>

  <footer class="abs footer"></footer>
  <div class="abs foot-card">
    <div class="abs foot-mark"></div>
    <div class="abs foot-name">Tallowmere Object Works, LLC</div>
    <div class="abs foot-tag">What you want...<br>NOW!</div>
  </div>
  <nav class="abs foot-links"><span>HOME</span><b>|</b><span>CONTACT</span><b>|</b><span>FRANCHISE</span><b>|</b><span>DISTRIBUTORS</span><b>|</b><span>CART</span></nav>
  <div class="abs foot-photo"><div class="photo" role="img" aria-label="Photo of a 3D printed lattice shoe"></div></div>
  <div class="abs foot-title">At vero eos et accusam</div>
  <p class="abs foot-copy">Duis autem vel eum iriure dolor in hendrerit in vulputate velit esse molestie consequat.</p>
  <div class="abs read-btn">Read more</div>
  <div class="abs social"><span></span><span></span><span></span><span></span><span></span></div>
  <div class="abs legal">2012 © Copyright - Tallowmere Object Works, LLC</div>

</div>
</body>
</html>
```